Stonebridge Building and Projects business cards

A business card with watermark background (construction work)

Company logo attached

Home improvement projects
House renovations
Bathroom and kitchen renovations
House extensions
New builds and granny flats

Director Omar Haddani
(Phone number)
omar@sbpbuilding.com.au
(Instagram logo) sbp_building

```html
<!DOCTYPE html>
<html lang="en">
<head>
<meta charset="utf-8">
<title>Stonebridge Building and Projects – Business Cards</title>
<link rel="stylesheet" href="https://fonts.googleapis.com/css2?family=Roboto:wght@400;500;700&display=swap">
<style>
  :root {
    --bg: #2a2a2c;
    --card: #141416;
    --card-edge: #1c1c1f;
    --blue: #1a87d0;
    --white: #f2f2f2;
    --muted: #c9c9cc;
    --emboss: #4a4a50;
  }
  * { box-sizing: border-box; margin: 0; padding: 0; }
  html, body { width: 1200px; height: 1050px; overflow: hidden; }
  body {
    background: var(--bg);
    font-family: "Roboto", Arial, sans-serif;
    position: relative;
  }
  .card {
    position: absolute;
    width: 640px;
    height: 370px;
    border-radius: 26px;
    background: linear-gradient(135deg, var(--card-edge), var(--card));
    overflow: hidden;
    box-shadow: 0 18px 40px rgba(0,0,0,.45);
  }
  .card--front { left: 90px; top: 110px; }
  .card--back  { left: 470px; top: 560px; }

  /* front */
  .watermark {
    position: absolute; right: 0; top: 0; width: 360px; height: 100%;
    background: radial-gradient(ellipse at 70% 30%, rgba(70,70,78,.35), rgba(20,20,22,0) 70%);
  }
  .brand {
    position: absolute; left: 44px; top: 128px; width: 270px;
  }
  .brand__name {
    color: var(--white); font-weight: 500;
    font-size: 26px; line-height: 1.2;
  }
  .brand__tagline {
    margin-top: 12px; padding-top: 8px; border-top: 2px solid var(--blue);
    color: var(--blue); font-size: 17px; font-weight: 500;
  }
  .contact {
    position: absolute; left: 340px; top: 92px;
  }
  .contact__name { color: var(--blue); font-size: 25px; font-weight: 700; }
  .contact__role { color: var(--white); font-size: 15px; margin: 4px 0 18px; }
  .contact__list { list-style: none; }
  .contact__item {
    display: flex; align-items: center; gap: 12px;
    color: var(--white); font-size: 15px; margin-bottom: 9px;
  }
  .icon { width: 16px; height: 16px; flex: none; }

  /* back */
  .back__name {
    position: absolute; left: 0; right: 0; top: 70px; text-align: center;
    color: var(--emboss); font-weight: 500; font-size: 40px; line-height: 1.2;
  }
  .services {
    position: absolute; left: 0; right: 0; top: 218px; height: 78px;
    background: var(--blue); color: var(--white);
    display: flex; flex-direction: column; justify-content: center; align-items: center;
    font-size: 16px; line-height: 1.55;
  }
  .footer {
    position: absolute; left: 0; right: 0; bottom: 30px;
    display: flex; justify-content: center; gap: 34px;
    color: var(--white); font-size: 15px;
  }
  .footer__item { display: flex; align-items: center; gap: 8px; }
  .dot { width: 14px; height: 14px; border-radius: 50%; border: 2px solid var(--blue); flex: none; }
</style>
</head>
<body>

<section class="card card--front">
  <div class="watermark" role="img" aria-label="Faint background image of construction work"></div>

  <div class="brand">
    <div class="brand__name">Stonebridge Building and Projects</div>
    <div class="brand__tagline">Built on solid ground!</div>
  </div>

  <div class="contact">
    <div class="contact__name">Omar Haddani</div>
    <div class="contact__role">Managing Director</div>
    <ul class="contact__list">
      <li class="contact__item">
        <svg class="icon" viewBox="0 0 16 16"><path d="M4 1.5l2.5 3-1.6 1.6a9 9 0 0 0 5 5l1.6-1.6 3 2.5-1.8 2.3C7 14 2 9 1.7 3.3z" fill="none" stroke="#1a87d0" stroke-width="1.4"/></svg>
        0400 318 275
      </li>
      <li class="contact__item">
        <svg class="icon" viewBox="0 0 16 16"><rect x="1.5" y="3.5" width="13" height="9" fill="none" stroke="#1a87d0" stroke-width="1.4"/><path d="M1.5 3.5L8 9l6.5-5.5" fill="none" stroke="#1a87d0" stroke-width="1.4"/></svg>
        omar@sbpbuilding.com.au
      </li>
      <li class="contact__item">
        <svg class="icon" viewBox="0 0 16 16"><circle cx="8" cy="8" r="6.5" fill="none" stroke="#1a87d0" stroke-width="1.4"/><path d="M1.5 8h13M8 1.5c-3 3.5-3 9.5 0 13M8 1.5c3 3.5 3 9.5 0 13" fill="none" stroke="#1a87d0" stroke-width="1.2"/></svg>
        sbpbuilding.com.au
      </li>
      <li class="contact__item">
        <span class="dot"></span>
        sbp_building
      </li>
    </ul>
  </div>
</section>

<section class="card card--back">
  <div class="back__name">Stonebridge Building<br>and Projects</div>
  <div class="services">
    <div>Home Improvement Projects | House Renovations | House Extensions</div>
    <div>Bathroom &amp; Kitchen Renovations | New Builds &amp; Granny Flats</div>
  </div>
  <div class="footer">
    <span class="footer__item"><span class="dot"></span>sbp_building</span>
    <span class="footer__item">
      <svg class="icon" viewBox="0 0 16 16"><circle cx="8" cy="8" r="6.5" fill="none" stroke="#1a87d0" stroke-width="1.4"/><path d="M1.5 8h13M8 1.5c-3 3.5-3 9.5 0 13M8 1.5c3 3.5 3 9.5 0 13" fill="none" stroke="#1a87d0" stroke-width="1.2"/></svg>
      sbpbuilding.com.au
    </span>
  </div>
</section>

</body>
</html>
```